Telecommunications/Power civil contractor needs business card design

Were a new telecommunications/power underground civil contractor that is looking for a new business card design. Our company colours are silver or grey and orange. Feel free to use the white background logo or the black background logo.

Target Market(s)

Local contractors, utility companies, private sector mining/energy companies, developers.

Industry/Entity Type

Telecommunications

Contact Information for Business Card

Each card will need the following info:
Persons name:
Title:
E-mail:
Phone number:
Shop Address:
Mailing Address:

Requirements
Must have
• Each card will need the following info:
• Persons name:
• Title:
• E-mail:
• Phone number:
• Shop Address:
• Mailing Address:

```html
<!DOCTYPE html>
<html lang="en">
<head>
<meta charset="utf-8">
<title>Ridgeline Contracting Inc – Business Card</title>
<link rel="stylesheet" href="https://fonts.googleapis.com/css2?family=Arimo:wght@400;700&display=swap">
<style>
  :root {
    --backdrop: #2b2b2b;
    --card-white: #f4f4f4;
    --brand-orange: #e2531f;
    --brand-grey: #5b5b5d;
    --ring-grey: #6f6f72;
    --ink: #1e1e1e;
    --ink-on-grey: #141414;
    --icon-on-grey: #e6e6e6;
  }
  * { box-sizing: border-box; margin: 0; padding: 0; }
  html, body {
    width: 1200px; height: 997px; overflow: hidden;
    background: var(--backdrop);
    font-family: "Arimo", Arial, sans-serif;
  }
  .business-card {
    position: absolute; left: 180px; top: 258px;
    width: 840px; height: 480px;
    border-radius: 26px; overflow: hidden;
    background: var(--card-white);
    box-shadow: 0 20px 50px rgba(0,0,0,.45);
  }
  .card-waves { position: absolute; inset: 0; }
  .brand {
    position: absolute; left: 56px; top: 60px;
    display: flex; flex-direction: column; align-items: flex-start; gap: 12px;
  }
  .brand-dot {
    width: 46px; height: 46px; border-radius: 50%;
    background: var(--brand-orange);
  }
  .brand-name {
    color: var(--brand-orange); font-weight: 700;
    font-size: 24px; line-height: 1.1; letter-spacing: .5px;
    text-transform: uppercase;
  }
  .person {
    position: absolute; right: 56px; top: 48px; text-align: right;
  }
  .person-name {
    color: var(--brand-orange); font-weight: 700; font-size: 30px;
  }
  .person-title {
    color: var(--ink); font-size: 17px; margin-top: 6px;
  }
  .contact-list {
    position: absolute; left: 56px; top: 334px;
    list-style: none; color: var(--ink-on-grey); font-size: 19px;
  }
  .contact-list li {
    display: flex; align-items: center; gap: 16px; height: 40px;
  }
  .contact-icon { width: 22px; height: 22px; flex: none; color: var(--icon-on-grey); }
  .addresses {
    position: absolute; right: 56px; top: 352px;
    text-align: right; color: var(--ink-on-grey);
    font-size: 15px; line-height: 21px; font-style: normal;
  }
  .address-block + .address-block { margin-top: 10px; }
  .address-label { font-weight: 700; }
</style>
</head>
<body>
  <section class="business-card">
    <svg class="card-waves" viewBox="0 0 840 480" width="840" height="480" aria-hidden="true">
      <path fill="var(--brand-orange)" d="M0,292 C200,222 420,242 560,260 C680,275 760,248 840,212 L840,480 L0,480 Z"/>
      <path fill="var(--brand-grey)" d="M0,330 C200,255 420,262 560,276 C680,289 760,262 840,228 L840,480 L0,480 Z"/>
      <circle cx="700" cy="262" r="64" fill="var(--card-white)" stroke="var(--ring-grey)" stroke-width="8"/>
    </svg>

    <div class="brand">
      <span class="brand-dot"></span>
      <span class="brand-name">Ridgeline<br>Contracting Inc</span>
    </div>

    <div class="person">
      <div class="person-name">Dana Marlow</div>
      <div class="person-title">Director</div>
    </div>

    <ul class="contact-list">
      <li>
        <svg class="contact-icon" viewBox="0 0 24 24" aria-hidden="true"><rect x="6" y="2" width="12" height="20" rx="2" fill="none" stroke="currentColor" stroke-width="2"/><circle cx="12" cy="18" r="1.3" fill="currentColor"/></svg>
        <span>5550142876</span>
      </li>
      <li>
        <svg class="contact-icon" viewBox="0 0 24 24" aria-hidden="true"><rect x="2" y="5" width="20" height="14" rx="1.5" fill="none" stroke="currentColor" stroke-width="2"/><path d="M2.5 6 12 13 21.5 6" fill="none" stroke="currentColor" stroke-width="2"/></svg>
        <span>info@ridgelinecontracting.com</span>
      </li>
      <li>
        <svg class="contact-icon" viewBox="0 0 24 24" aria-hidden="true"><circle cx="12" cy="12" r="9.5" fill="none" stroke="currentColor" stroke-width="2"/><path d="M2.5 12h19M12 2.5c3 3 3 16 0 19M12 2.5c-3 3-3 16 0 19" fill="none" stroke="currentColor" stroke-width="1.6"/></svg>
        <span>www.ridgelinecontracting.com</span>
      </li>
    </ul>

    <address class="addresses">
      <div class="address-block">
        <div class="address-label">Shop Address</div>
        <div>1420 Quarry Road, Dunmore, NV 89001</div>
      </div>
      <div class="address-block">
        <div class="address-label">Mailing Address</div>
        <div>PO Box 318, Dunmore, NV 89001</div>
      </div>
    </address>
  </section>
</body>
</html>
```